Business card design for a dynamic IT consulting company

We need a business card design for a young firm, specialized in the Telecommunications/Consulting industry. The name of the company is Quindor and Partners Business Consulting Ltd. (Short name: Quindor and Partnes)
Quindor = solve read reverse, so we aim to be uncomplicated and solution-oriented. The small pipe in our logo is also related to the word solve. So we need a new business card design, which is simple, eye catching and something non traditional (I would probably prefer a square shaped design rather than a rectangle, but open for suggestions). Attached our logo.

Target Market(s)

Usually our customers are Tier1 Telecoms providers (Q-Netra, Palorix, etc) and their executives.

Industry/Entity Type

Business

Contact Information for Business Card

Name: Bence Tolnavari
Email: b.tolnavari@quindor.hu
Web: www.quindor.hu
Mobile: +36 30 518 2769
Title: Managing Director

Optional:
Company name: Quindor and Partners Ltd.
Address: 1087 Budapest, Tolvenka str. 28/C, Hungary

Font styles to use
Other font styles liked:
• helveticaneue_medium, Prime Regular are used now.

Colors

Designer to choose colors to be used in the design.

Requirements
Must have
• I would like to have a 2 sided design.
Nice to have
• I thought if we make the logo a bit bigger (without the company name), that could go to the back with the company name below. I though, if the pipe in the logo is somehow touchable on the business card, would be nice and unique.

```html
<!DOCTYPE html>
<html lang="en">
<head>
<meta charset="utf-8">
<title>Quindor and Partners – Business Card</title>
<link rel="stylesheet" href="https://fonts.googleapis.com/css2?family=Comfortaa:wght@500;700&family=Roboto:wght@400;500&display=swap">
<style>
  :root {
    --backdrop: #1e1e20;
    --card-ink: #333335;
    --paper: #ffffff;
    --magenta: #b5309a;
    --cyan: #1a9ad6;
    --slate: #5a5b5d;
    --text-dark: #3a3a3c;
    --text-light: #ffffff;
  }
  * { box-sizing: border-box; margin: 0; padding: 0; }
  html, body {
    width: 1200px; height: 880px; overflow: hidden;
    background: var(--backdrop);
  }
  .canvas {
    width: 1200px; height: 880px;
    display: flex; flex-direction: column; align-items: center; justify-content: center;
    gap: 34px;
  }
  .card {
    position: relative;
    width: 700px; height: 400px;
    border-radius: 24px;
    background: var(--card-ink);
    overflow: hidden;
    box-shadow: 0 12px 30px rgba(0,0,0,.45);
  }

  /* ---------- wordmark ---------- */
  .wordmark {
    display: flex; align-items: center; gap: 12px;
    font-family: "Comfortaa", sans-serif; font-weight: 700;
    color: var(--text-light);
    letter-spacing: -0.5px;
    white-space: nowrap;
  }
  .wordmark__square {
    width: 14px; height: 14px; background: var(--magenta);
    flex: none;
  }

  /* ---------- back side ---------- */
  .card--back .tile-field {
    position: absolute; left: 0; top: 0; bottom: 0; width: 330px;
    background: linear-gradient(150deg,
      rgba(181,48,154,.45) 0%,
      rgba(26,154,214,.40) 40%,
      rgba(90,91,93,.45) 75%,
      rgba(51,51,53,0) 100%);
  }
  .card--back .wordmark {
    position: absolute; right: 48px; top: 200px;
    font-size: 38px;
  }

  /* ---------- front side ---------- */
  .front__header {
    position: absolute; left: 0; right: 0; top: 0; height: 118px;
    display: flex; align-items: center; padding-left: 130px;
  }
  .front__header .wordmark { font-size: 48px; }

  .front__band {
    position: absolute; left: 0; right: 0; top: 126px; height: 176px;
    background: var(--paper);
    display: flex; align-items: center;
  }
  .front__rule { position: absolute; left: 0; right: 0; height: 2px; }
  .front__rule--top { top: 121px; background: var(--cyan); }
  .front__rule--bottom { top: 306px; background: var(--magenta); }

  .front__tile-field {
    width: 230px; height: 130px; margin-left: 50px;
    border-radius: 6px;
    background: linear-gradient(120deg,
      rgba(181,48,154,.22) 0%,
      rgba(26,154,214,.22) 55%,
      rgba(90,91,93,.22) 100%);
  }
  .front__divider {
    width: 1px; height: 118px; background: var(--magenta);
    margin: 0 32px 0 40px;
  }
  .contact__name {
    font-family: "Comfortaa", sans-serif; font-weight: 700;
    font-size: 24px; color: var(--text-dark);
  }
  .contact__title {
    font-family: "Roboto", sans-serif; font-weight: 500;
    font-size: 16px; color: var(--magenta); margin: 2px 0 12px;
  }
  .contact__list { list-style: none; }
  .contact__item {
    display: flex; align-items: center; gap: 9px;
    font-family: "Roboto", sans-serif; font-size: 15px; color: var(--text-dark);
    line-height: 22px;
  }
  .contact__icon { width: 15px; height: 15px; flex: none; }

  .front__footer {
    position: absolute; left: 0; right: 0; top: 308px; bottom: 0;
    display: flex; flex-direction: column; justify-content: center; align-items: center;
    color: var(--text-light); text-align: center;
  }
  .company__name {
    font-family: "Roboto", sans-serif; font-weight: 500; font-size: 19px;
  }
  .company__address {
    font-family: "Roboto", sans-serif; font-size: 15px; margin-top: 3px;
  }
</style>
</head>
<body>
<main class="canvas">

  <section class="card card--back" aria-label="Card back">
    <div class="tile-field" role="img" aria-label="Decorative scattered magenta, blue and grey tiles"></div>
    <div class="wordmark"><span class="wordmark__square"></span>Quindor &amp; Partners</div>
  </section>

  <section class="card card--front" aria-label="Card front">
    <header class="front__header">
      <div class="wordmark"><span class="wordmark__square"></span>Quindor &amp; Partners</div>
    </header>

    <div class="front__rule front__rule--top"></div>
    <div class="front__band">
      <div class="front__tile-field" role="img" aria-label="Decorative tile motif in magenta, blue and grey"></div>
      <div class="front__divider"></div>
      <div class="contact">
        <p class="contact__name">Bence Tolnavari</p>
        <p class="contact__title">Managing Director</p>
        <ul class="contact__list">
          <li class="contact__item">
            <svg class="contact__icon" viewBox="0 0 16 16"><rect width="16" height="16" fill="var(--magenta)"/><rect x="5" y="3" width="6" height="10" rx="1" fill="none" stroke="#fff" stroke-width="1.4"/></svg>
            +36 30 518 2769
          </li>
          <li class="contact__item">
            <svg class="contact__icon" viewBox="0 0 16 16"><rect width="16" height="16" fill="var(--slate)"/><rect x="3" y="4.5" width="10" height="7" fill="none" stroke="#fff" stroke-width="1.2"/><path d="M3 4.5 L8 9 L13 4.5" fill="none" stroke="#fff" stroke-width="1.2"/></svg>
            b.tolnavari@quindor.hu
          </li>
          <li class="contact__item">
            <svg class="contact__icon" viewBox="0 0 16 16"><rect width="16" height="16" fill="var(--cyan)"/><circle cx="8" cy="8" r="5" fill="none" stroke="#fff" stroke-width="1.1"/><ellipse cx="8" cy="8" rx="2.2" ry="5" fill="none" stroke="#fff" stroke-width="1"/><path d="M3 8 H13" stroke="#fff" stroke-width="1"/></svg>
            www.quindor.hu
          </li>
        </ul>
      </div>
    </div>
    <div class="front__rule front__rule--bottom"></div>

    <footer class="front__footer">
      <p class="company__name">Quindor and Partners Ltd.</p>
      <p class="company__address">1087 Budapest, Tolvenka str. 28/C, Hungary</p>
    </footer>
  </section>

</main>
</body>
</html>
```